Wandering Rooms Stationary Set

Wandering Rooms is a bespoke interior design firm set to provide services to VIP clients with elegance and minimalism is the main theme for our stationary set. We require a full stationary set covering A4 letterhead, A4 & A3 envelopes, business cards, USB's, CDs, email signature and any other item the designer sees fit. logo is already designed and finalized, and we require the designer to use it as is without modifying the logo.

Address to be used on letterhead / business cards ...etc shall be as follows:

Phone : +971 2 518 2047
P.O. Box : 309186
Address: Block C&D, Bldg. 47, Court 12, Abu Dhabi, United Arab Emirates
Website: www.wanderingrooms-example.com

Target Market(s)

VIP Clients

Industry/Entity Type

Interior Design

Font styles to use
Other font styles liked:
• something to be unique

Colors

Designer to choose colors to be used in the design.

Requirements
Must have
• Elegant, minimalistic
Nice to have
• Simple yet elegant design having a sharp yet clean cut format
Should not have
• No additional colours, just colours that are used in the logo (silver, black or gold)

```html
<!DOCTYPE html>
<html lang="en">
<head>
<meta charset="utf-8">
<title>Wandering Rooms — Business Card</title>
<link rel="stylesheet" href="https://fonts.googleapis.com/css2?family=Cormorant+Garamond:wght@400;500&family=Great+Vibes&display=swap">
<style>
  :root {
    --backdrop: #1b1b1c;
    --card: #262627;
    --card-edge: #2e2e2f;
    --gold: #b89a5c;
    --gold-text: #c4a465;
    --ink: #1a1a1a;
    --silver: #4a4a4c;
    --grey-text: #b8b8b8;
  }
  * { box-sizing: border-box; margin: 0; padding: 0; }
  html, body { width: 1200px; height: 800px; overflow: hidden; background: var(--backdrop); }
  body { font-family: "Cormorant Garamond", "Times New Roman", serif; }

  .stage { position: relative; width: 1200px; height: 800px; }

  .card {
    position: absolute;
    top: 245px;
    width: 520px;
    height: 300px;
    background: var(--card);
    border: 1px solid var(--card-edge);
  }
  .card--front { left: 50px; }
  .card--back { left: 630px; }

  .wordmark {
    font-family: "Cormorant Garamond", "Times New Roman", serif;
    font-weight: 500;
    text-transform: uppercase;
    letter-spacing: 0.22em;
    white-space: nowrap;
  }
  .card--front .wordmark {
    position: absolute;
    left: 0; right: 0; top: 128px;
    text-align: center;
    font-size: 34px;
    color: var(--silver);
  }

  .holder {
    position: absolute;
    right: 28px; top: 28px;
    text-align: right;
  }
  .holder__name {
    font-family: "Great Vibes", cursive;
    font-size: 30px;
    color: var(--gold-text);
    line-height: 1;
  }
  .holder__title {
    font-size: 15px;
    color: var(--grey-text);
    margin-top: 2px;
  }

  .card--back .wordmark {
    position: absolute;
    left: 40px; top: 112px;
    font-size: 25px;
    color: var(--gold-text);
  }

  .info-band {
    position: absolute;
    left: 0; right: 0;
    top: 165px; height: 118px;
    background: var(--gold);
    color: var(--ink);
  }
  .contacts {
    position: absolute;
    right: 22px; top: 14px;
    list-style: none;
    font-size: 13px;
    line-height: 17px;
    text-align: right;
  }
  .contacts li { display: flex; justify-content: flex-end; align-items: center; gap: 7px; }
  .contacts svg { width: 10px; height: 10px; fill: var(--ink); }
  .address {
    position: absolute;
    left: 40px; bottom: 12px;
    font-size: 13px;
    line-height: 16px;
    font-style: normal;
  }
</style>
</head>
<body>
<main class="stage">

  <section class="card card--front" aria-label="Business card front">
    <p class="wordmark">Wandering Rooms</p>
  </section>

  <section class="card card--back" aria-label="Business card back">
    <div class="holder">
      <p class="holder__name">Daniel Hartley</p>
      <p class="holder__title">President</p>
    </div>

    <p class="wordmark">Wandering Rooms</p>

    <div class="info-band">
      <ul class="contacts">
        <li>+971 2 518 2047
          <svg viewBox="0 0 10 10" aria-hidden="true"><path d="M2 0.5 L3.6 2.8 L2.6 3.8 C3.3 5.3 4.7 6.7 6.2 7.4 L7.2 6.4 L9.5 8 L8.4 9.5 C4.5 9.2 0.8 5.5 0.5 1.6 Z"/></svg>
        </li>
        <li>info@wanderingrooms-example.com
          <svg viewBox="0 0 10 10" aria-hidden="true"><path d="M0.5 2 H9.5 V8.5 H0.5 Z M1.2 2.6 L5 5.6 L8.8 2.6" fill="none" stroke="#1a1a1a" stroke-width="1"/></svg>
        </li>
        <li>www.wanderingrooms-example.com
          <svg viewBox="0 0 10 10" aria-hidden="true"><circle cx="5" cy="5" r="4.5"/></svg>
        </li>
      </ul>
      <address class="address">
        P.O. Box : 309186<br>
        Block C&amp;D, Bldg. 47, Court 12<br>
        Abu Dhabi, United Arab Emirates
      </address>
    </div>
  </section>

</main>
</body>
</html>
```